Heron Haulage needs Bussiness cards!

Our new trucking company needs business cards!
We need the same design with two different names and emails, everything else it's the same.
I have included our original logo so we can use it for the design.
Note: the logo to be used is the o e with the buffalo on the right side, next to the letters H and H.

Target Market(s)

Trucking, refrigerated transportation, freight

Industry/Entity Type

Business

Contact Information for Business Card

Card #1:
Marcus Whitfield
marcuswhitfield@heronhaulage.example
1-855-317-6094
(956)238-7160
4117 W. Larkin Ave.
Pharr, TX 78590
www.heronhaulage.example

Card#2:
Rosalba Quintero
rosalba@heronhaulage.example
1-855-317-6094
(956)238-7160
4117 W. Larkin Ave.
Pharr, TX 78590
www.heronhaulage.example

Font styles to use
Sans Serif

Colors
0655a3
ec1f27
ffffff

Requirements
Must have
• our logo
Nice to have
• roads on background,

```html
<!DOCTYPE html>
<html lang="en">
<head>
<meta charset="utf-8">
<title>Heron Haulage — Business Card</title>
<link href="https://fonts.googleapis.com/css2?family=Roboto:wght@400;500;700;900&display=swap" rel="stylesheet">
<style>
  :root {
    --brand-navy: #0b3a6e;
    --brand-blue: #0655a3;
    --brand-red: #ec1f27;
    --paper: #ffffff;
    --backdrop: #2e2f31;
  }
  * { margin: 0; padding: 0; box-sizing: border-box; }
  html, body {
    width: 1200px;
    height: 950px;
    overflow: hidden;
    background: var(--backdrop);
    font-family: "Roboto", Arial, sans-serif;
  }
  .stage {
    position: relative;
    width: 1200px;
    height: 950px;
  }
  .card {
    position: absolute;
    left: 250px;
    width: 700px;
    height: 400px;
    background: var(--paper);
    overflow: hidden;
    box-shadow: 0 12px 30px rgba(0,0,0,0.45);
  }
  .card--front { top: 50px; }
  .card--back { top: 500px; }

  .wordmark {
    position: absolute;
    display: flex;
    align-items: center;
    gap: 14px;
    white-space: nowrap;
  }
  .wordmark__dot {
    width: 30px;
    height: 30px;
    border-radius: 50%;
    background: var(--brand-red);
    flex: none;
  }
  .wordmark__name {
    font-weight: 900;
    color: var(--brand-navy);
    letter-spacing: -0.5px;
    line-height: 1;
  }
  .card--front .wordmark {
    left: 50%;
    top: 50%;
    transform: translate(-50%, -50%);
  }
  .card--front .wordmark__name { font-size: 54px; }

  .card--back .wordmark {
    left: 28px;
    top: 50%;
    transform: translateY(-50%);
    gap: 10px;
  }
  .card--back .wordmark__dot { width: 22px; height: 22px; }
  .card--back .wordmark__name { font-size: 31px; }

  .info-panel {
    position: absolute;
    inset: 0;
    width: 700px;
    height: 400px;
  }
  .contact {
    position: absolute;
    left: 330px;
    top: 78px;
    color: var(--paper);
  }
  .contact__name {
    font-size: 24px;
    font-weight: 700;
    margin-bottom: 34px;
  }
  .contact__address,
  .contact__lines {
    font-size: 15px;
    line-height: 22px;
    font-weight: 400;
  }
  .contact__address { margin-bottom: 22px; }
</style>
</head>
<body>
<main class="stage">

  <section class="card card--front" aria-label="Card front">
    <div class="wordmark">
      <span class="wordmark__dot"></span>
      <span class="wordmark__name">Heron Haulage</span>
    </div>
  </section>

  <section class="card card--back" aria-label="Card back">
    <svg class="info-panel" viewBox="0 0 700 400" aria-hidden="true">
      <polyline points="295,0 295,108 279,124 295,140 295,400"
                fill="none" stroke="var(--brand-red)" stroke-width="3"/>
      <polygon points="303,0 700,0 700,400 303,400 303,140 287,124 303,108"
               fill="var(--brand-navy)"/>
    </svg>

    <div class="wordmark">
      <span class="wordmark__dot"></span>
      <span class="wordmark__name">Heron Haulage</span>
    </div>

    <div class="contact">
      <p class="contact__name">Marcus Whitfield</p>
      <p class="contact__address">4117 W. Larkin Ave.<br>Pharr, TX 78590</p>
      <p class="contact__lines">
        Phone : 1-855-317-6094<br>
        Mobile : (956)238-7160<br>
        marcuswhitfield@heronhaulage.example<br>
        www.heronhaulage.example
      </p>
    </div>
  </section>

</main>
</body>
</html>
```